UK based media owner TALMOX (http://www.talmox.uk/) needs DIGITAL ADVERT to run on our digital panel

Hi guys,

Thanks for taking the time to have a look at this brief.
I need someone to create a digital advert (still/static design or video) to run on our digital panels which are located across UK university student unions.
For who wants to upload a video ---> All of our panels are digitally enabled and allow for full motion video – they run adverts 10 seconds long (see artwork specification document in attachment) therefore the advert will have to be 10 seconds long.
For static/still design ----> see artwork specification to see resolution etc

I need something professional looking, polished yet fresh and exciting so that it speaks and connects to this younger audience – we want to inspire them to take a step towards new levels of business opportunities.

Here are some Key Points you’ll need to take into consideration when designing the advert:

Overall Campaign Objective: To excite and attract young entrepreneurs to get in touch with us for possible partnerships

Target Audience: Young entrepreneurs attending university (university students – 18 to 24 years old)

Creative Specifications: See attached document with artwork specifications

Text on Advert:

I need the following text to appear on the advert: (Please include company logo)

“Do you have a business idea that would benefit with advertising on these screens?

We want to support young entrepreneurs and will partner with any whom have a great idea

WE WANT TO HEAR FROM YOU!

Email us at ideas@talmox.uk
www.talmox.uk/ideas”

I would need some ideas by the 3rd July 2018 if possible.

Thanks to all who will take part in this project – contact me if you have any questions

Low designer entries

Need extra days to review

Target Market(s)

Young entrepreneurs attending university (university students – 18 to 24 years old)

Requirements
Must have
• I need the following text to appear on the advert: (Please include company logo)
• “Do you have a business idea that would benefit with advertising on these screens?
• We want to support young entrepreneurs and will partner with any whom have a great idea
• WE WANT TO HEAR FROM YOU!
• Email us at ideas@talmox.uk
• www.talmox.uk/ideas”

```html
<!DOCTYPE html>
<html lang="en">
<head>
<meta charset="utf-8">
<title>TALMOX – We want to support young entrepreneurs</title>
<link rel="stylesheet" href="https://fonts.googleapis.com/css2?family=Open+Sans:wdth,wght@75,400;75,700;100,400&display=swap">
<style>
  :root {
    --brand-red: #b0101f;
    --cream: #fcf9cc;
    --sun-yellow: #fff200;
    --bubble-blue: #1aa0e1;
    --panel-grey: #bdbdbd;
    --panel-sky: #4fc4ec;
    --ink-dark: #454545;
    --headline-red: #c32a3f;
    --white: #ffffff;
  }
  * { margin: 0; padding: 0; box-sizing: border-box; }
  html, body { width: 675px; height: 1200px; overflow: hidden; background: var(--white); }
  .advert {
    position: relative;
    width: 675px;
    height: 1200px;
    overflow: hidden;
    font-family: "Open Sans", Arial, sans-serif;
    font-stretch: 75%;
  }
  .top-band {
    position: absolute; left: 0; top: 0; width: 675px; height: 68px;
    background: var(--brand-red);
  }
  .top-band .web-address {
    position: absolute; right: 42px; top: 18px;
    color: var(--white); font-size: 25px; font-weight: 400; font-stretch: 100%;
    letter-spacing: 0.5px;
  }
  .message-zone {
    position: absolute; left: 0; top: 68px; width: 675px; height: 332px;
    background: linear-gradient(90deg, var(--cream) 0%, var(--cream) 60%, var(--sun-yellow) 82%, var(--sun-yellow) 100%);
  }
  .opening-question {
    position: absolute; left: 30px; top: 72px; width: 620px;
    color: var(--ink-dark); font-size: 17px; font-weight: 700; line-height: 20px;
  }
  .photo-zone {
    position: absolute; left: 0; top: 400px; width: 675px; height: 400px;
    background: linear-gradient(100deg, #8c8c8c 0%, #d9d7d4 35%, #b6b2ae 60%, #6f6f6f 100%);
  }
  .audience-line {
    position: absolute; left: 30px; top: 744px;
    color: var(--white); font-size: 30px; font-weight: 700; line-height: 36px;
  }
  .speech-bubble { position: absolute; left: 0; top: 0; width: 675px; height: 560px; }
  .bubble-text {
    position: absolute; left: 60px; top: 150px; width: 332px;
    color: var(--bubble-blue); font-weight: 700; font-size: 86px; line-height: 104px;
    text-align: right; letter-spacing: -0.5px;
  }
  .bubble-text span { display: block; }
  .panel-left {
    position: absolute; left: 0; top: 800px; width: 338px; height: 336px; background: var(--panel-grey);
  }
  .panel-right {
    position: absolute; left: 338px; top: 800px; width: 337px; height: 336px; background: var(--panel-sky);
  }
  .pledge {
    position: absolute; color: var(--ink-dark); font-weight: 700; font-size: 54px; line-height: 1;
    letter-spacing: -0.5px; white-space: nowrap;
  }
  .pledge.first { left: 118px; top: 833px; }
  .pledge.second { left: 340px; top: 881px; }
  .headline {
    position: absolute; color: var(--headline-red); font-weight: 700; font-size: 73px; line-height: 1;
    opacity: 0.92; white-space: nowrap;
  }
  .headline.first { left: 117px; top: 961px; }
  .headline.second { left: 265px; top: 1033px; }
  .bottom-band {
    position: absolute; left: 0; top: 1136px; width: 675px; height: 64px; background: var(--brand-red);
  }
  .contact {
    position: absolute; left: 24px; top: 9px;
    color: var(--white); font-size: 19px; line-height: 23px;
  }
  .contact strong { display: block; font-weight: 700; }
  .brand-name {
    position: absolute; left: 374px; top: 8px;
    color: var(--white); font-size: 40px; font-weight: 400; font-stretch: 100%;
    letter-spacing: 14px; line-height: 48px;
  }
</style>
</head>
<body>
<main class="advert">
  <header class="top-band">
    <span class="web-address">www.talmox.uk/ideas</span>
  </header>

  <section class="message-zone"></section>
  <p class="opening-question">Do you have a business idea that would benefit with advertising on these screens?</p>

  <div class="photo-zone" role="img" aria-label="Photo of smiling young students gathered around a laptop"></div>
  <p class="audience-line">We want to support young entrepreneurs</p>

  <svg class="speech-bubble" viewBox="0 0 675 560" aria-hidden="true">
    <path d="M74 106 H468 Q500 106 500 138 V358 Q500 390 468 390 H408 V506 L290 390 H74 Q42 390 42 358 V138 Q42 106 74 106 Z"
          fill="var(--cream)" stroke="var(--bubble-blue)" stroke-width="22" stroke-linejoin="round"/>
  </svg>
  <h1 class="bubble-text">
    <span>We want</span>
    <span>support</span>
  </h1>

  <div class="panel-left"></div>
  <div class="panel-right"></div>

  <p class="pledge first">...and will partner</p>
  <p class="pledge second">with any...</p>
  <p class="headline first">WHOM HAVE</p>
  <p class="headline second">A GREAT IDEA</p>

  <footer class="bottom-band">
    <p class="contact"><strong>WE WANT TO HEAR FROM YOU!</strong>Email us at ideas@talmox.uk</p>
    <span class="brand-name">TALMOX</span>
  </footer>
</main>
</body>
</html>
```